Residential Remodeling Contractor needs updated business card

I need a new design for my business card.
Name of the company is Ridgefell Construction. I need a card that commands presence, strength, integrity. I have been in business for 28 years. I am a Residential Remodeling Contractor that covers all aspects of a residential remodel and build.

```html
<!DOCTYPE html>
<html lang="en">
<head>
<meta charset="utf-8">
<title>Ridgefell Construction – Business Card</title>
<link href="https://fonts.googleapis.com/css2?family=Cinzel:wght@600&family=Poppins:wght@400;600&display=swap" rel="stylesheet">
<style>
  :root {
    --backdrop: #9b9b9b;
    --navy: #1f3c7c;
    --paper: #ffffff;
    --ink: #2b2b2b;
    --rule: #c4c4c4;
  }
  * { margin: 0; padding: 0; box-sizing: border-box; }
  html, body { width: 1093px; height: 1200px; overflow: hidden; }
  body { background: var(--backdrop); position: relative; font-family: "Poppins", sans-serif; }

  .card {
    position: absolute;
    left: 265px;
    height: 356px;
    border-radius: 30px;
  }
  .card--front { top: 226px; width: 576px; background: var(--paper); }
  .card--back  { top: 621px; width: 580px; background: var(--navy); }

  .brand-mark {
    position: absolute;
    display: block;
  }
  .brand-name {
    position: absolute;
    font-family: "Poppins", sans-serif;
    font-weight: 600;
    line-height: 1.1;
    white-space: nowrap;
  }
  .brand-name span { display: block; }

  .card--front .brand-mark {
    left: 40px;
    top: 165px;
    width: 26px;
    height: 26px;
    background: var(--navy);
  }
  .card--front .brand-name {
    left: 80px;
    top: 148px;
    color: var(--navy);
    font-size: 26px;
  }

  .divider {
    position: absolute;
    left: 288px;
    top: 74px;
    width: 1px;
    height: 209px;
    background: var(--rule);
  }

  .contact {
    position: absolute;
    left: 306px;
    top: 90px;
    color: var(--ink);
  }
  .contact__name {
    font-family: "Cinzel", serif;
    font-weight: 600;
    color: var(--navy);
    font-size: 22px;
    line-height: 1;
  }
  .contact__role { font-size: 17px; line-height: 1.2; margin-top: 1px; }
  .contact__list { list-style: none; margin-top: 12px; }
  .contact__item {
    display: flex;
    align-items: center;
    gap: 7px;
    font-size: 17px;
    line-height: 21px;
  }
  .contact__item svg { width: 15px; height: 15px; flex: none; color: var(--navy); }
  .contact__domain { color: var(--navy); }
  .contact__address { font-size: 17px; line-height: 21px; margin-top: 13px; }

  .card--back .brand-mark {
    left: 102px;
    top: 165px;
    width: 44px;
    height: 44px;
    background: var(--paper);
  }
  .card--back .brand-name {
    left: 168px;
    top: 136px;
    color: var(--paper);
    font-size: 46px;
  }
</style>
</head>
<body>
  <section class="card card--front">
    <span class="brand-mark" role="img" aria-label="Ridgefell Construction emblem"></span>
    <h1 class="brand-name"><span>Ridgefell</span><span>Construction</span></h1>
    <div class="divider"></div>
    <div class="contact">
      <p class="contact__name">Daniel Hartwell</p>
      <p class="contact__role">Managing Director</p>
      <ul class="contact__list">
        <li class="contact__item">
          <svg viewBox="0 0 24 24" aria-hidden="true"><path fill="currentColor" d="M6.6 10.8a15.1 15.1 0 0 0 6.6 6.6l2.2-2.2a1 1 0 0 1 1-.25 11.4 11.4 0 0 0 3.6.57 1 1 0 0 1 1 1V20a1 1 0 0 1-1 1A17 17 0 0 1 3 4a1 1 0 0 1 1-1h3.5a1 1 0 0 1 1 1c0 1.25.2 2.45.57 3.57a1 1 0 0 1-.25 1z"/></svg>
          044-987 654 321
        </li>
        <li class="contact__item">
          <svg viewBox="0 0 24 24" aria-hidden="true"><path fill="currentColor" d="M2 5h20v14H2zm2 2v.4l8 5.3 8-5.3V7zm0 2.8V17h16V9.8l-8 5.3z"/></svg>
          info@ridgefellbuild.com
        </li>
        <li class="contact__item">
          <svg viewBox="0 0 24 24" aria-hidden="true"><g fill="none" stroke="currentColor" stroke-width="2"><circle cx="12" cy="12" r="9"/><path d="M3 12h18M12 3c3 3 3 15 0 18M12 3c-3 3-3 15 0 18"/></g></svg>
          <span>www.<span class="contact__domain">ridgefellbuild</span>.com</span>
        </li>
      </ul>
      <p class="contact__address">421, Address line goes here<br>45452,Country Name</p>
    </div>
  </section>

  <section class="card card--back">
    <span class="brand-mark" role="img" aria-label="Ridgefell Construction emblem"></span>
    <p class="brand-name"><span>Ridgefell</span><span>Construction</span></p>
  </section>
</body>
</html>
```